Tollin Waste Website Design

Our new start-up needs a website design. We plan to help businesses find more sustainable ways to manage their waste. Our initial website aims to gather contact data from potential business customers and comprehensive information from waste facilities and waste transporters. We have a logo design (attached) which we would like included in the website design. I have also attached a number of pages that describe what information should appear on each page as well as a web design brief file that describes the look we are after.

```html
<!DOCTYPE html>
<html lang="en">
<head>
<meta charset="utf-8">
<title>Tollin Waste – Waste Transporters</title>
<link href="https://fonts.googleapis.com/css2?family=Poppins:wght@400;500&family=Roboto:ital,wght@0,400;1,400&display=swap" rel="stylesheet">
<style>
:root{
  --green:#5b9a2b;
  --ink:#1c1c1c;
  --text:#333333;
  --muted:#8c8c8c;
  --line:#c4c4c4;
  --page:#f2f2f2;
  --card:#ffffff;
  --footer:#0b0b0b;
}
*{box-sizing:border-box;margin:0;padding:0}
html,body{width:1200px;height:2184px;overflow:hidden;background:var(--page);font-family:"Roboto",sans-serif;color:var(--text)}
.site-header{position:absolute;left:0;top:0;width:1200px;height:122px}
.header-photo{position:absolute;inset:0;background:linear-gradient(90deg,#f3f6ef 0%,#eef3e8 45%,#dfe8d5 75%,#cfdcc2 100%)}
.brand{position:absolute;left:90px;top:44px;display:flex;align-items:center;gap:10px;font-family:"Poppins",sans-serif;font-weight:500;font-size:26px;color:var(--green)}
.brand-dot{width:30px;height:30px;border-radius:50%;background:var(--green)}
.main-nav{position:absolute;top:48px;font-family:"Poppins",sans-serif;font-size:18px;color:#222}
.main-nav a{position:absolute;white-space:nowrap;color:inherit;text-decoration:none}
.social{position:absolute;top:47px;left:969px;display:flex;gap:10px}
.social span{width:28px;height:28px;border:2px solid #333;border-radius:50%}
.intro{position:absolute;top:190px;left:0;width:1200px;text-align:center}
.intro h1{font-family:"Poppins",sans-serif;font-weight:400;font-size:43px;color:var(--ink);line-height:56px}
.intro h1 em{font-style:normal;color:var(--green)}
.intro p{width:900px;margin:22px auto 0;font-size:15.5px;line-height:32px;color:#333}
.form-card{position:absolute;left:92px;top:427px;width:1019px;height:1524px;background:var(--card);box-shadow:0 1px 6px rgba(0,0,0,.12)}
.form-grid{position:absolute;left:0;top:474px;width:1200px}
.row{position:absolute;left:0;width:1200px;height:73px;display:flex;align-items:center}
.row label.caption{position:absolute;right:702px;width:420px;text-align:right;font-size:16.5px;line-height:26px;color:#333}
.field{position:absolute;left:540px;width:494px;height:54px;border:1.5px solid var(--line);background:#fff;display:flex;align-items:center;padding:0 16px;font-size:16px;color:#444}
.field.hint{font-style:italic;color:var(--muted);font-size:15px}
.field.half{width:242px}
.field.half.second{left:791px;width:243px}
.field svg{position:absolute;right:14px}
.radios{position:absolute;left:543px;display:flex;font-size:16.5px;color:#333}
.radio{display:flex;align-items:center;gap:8px;width:95px}
.dot{width:16px;height:16px;border-radius:50%;border:1.5px solid #777;display:flex;align-items:center;justify-content:center}
.dot.on{border-color:var(--green)}
.dot.on::after{content:"";width:8px;height:8px;border-radius:50%;background:var(--green)}
.submit{position:absolute;left:517px;top:1848px;width:167px;height:46px;border-radius:23px;background:var(--green);color:#fff;font-family:"Poppins",sans-serif;font-weight:500;font-size:22px;display:flex;align-items:center;justify-content:center}
.site-footer{position:absolute;left:0;top:2092px;width:1200px;height:92px;background:var(--footer);color:#fff;font-size:18px;display:flex;align-items:center;justify-content:center}
</style>
</head>
<body>
<header class="site-header">
  <div class="header-photo" role="img" aria-label="Faded photo of green forest trees"></div>
  <div class="brand"><span class="brand-dot"></span>Tollin Waste</div>
  <nav class="main-nav">
    <a style="left:331px">About us</a>
    <a style="left:436px">What we do</a>
    <a style="left:558px">Resources</a>
    <a style="left:668px">Contact us</a>
  </nav>
  <div class="social" aria-label="Social links"><span></span><span></span><span></span><span></span></div>
</header>

<section class="intro">
  <h1><em>Waste</em> Transporters</h1>
  <p>Waste transporters and controlled waste carriers provide a vital link between waste producers and waste facilities. The safe transport of waste is an essential economic and community service. By registering your waste transportation services with Tollin Waste your business will be visible to waste producers looking for waste transport options.</p>
</section>

<div class="form-card"></div>
<form class="form-grid">
  <div class="row" style="top:0"><label class="caption">Registered business name</label><div class="field"></div></div>
  <div class="row" style="top:72px"><label class="caption">Trading as (if applicable)</label><div class="field"></div></div>
  <div class="row" style="top:145px"><label class="caption">Business address</label><div class="field"></div></div>
  <div class="row" style="top:218px"><label class="caption">Post code</label><div class="field"></div></div>
  <div class="row" style="top:290px"><label class="caption">Email contact</label><div class="field"></div></div>
  <div class="row" style="top:364px"><label class="caption">Phone contact</label><div class="field"></div></div>
  <div class="row" style="top:437px"><label class="caption">Regions of operation</label><div class="field">Select<svg width="12" height="7" viewBox="0 0 12 7"><path d="M0 0h12L6 7z" fill="#333"/></svg></div></div>
  <div class="row" style="top:510px"><label class="caption">Days and times for collection</label>
    <div class="field half">Date<svg width="16" height="16" viewBox="0 0 16 16"><rect x="1.5" y="3" width="13" height="11.5" fill="none" stroke="#444" stroke-width="1.4"/><path d="M1.5 6.5h13M5 1v4M11 1v4M4 9h2M7 9h2M10 9h2M4 11.5h2M7 11.5h2" stroke="#444" stroke-width="1.4"/></svg></div>
    <div class="field half second">Time<svg width="17" height="17" viewBox="0 0 17 17"><circle cx="8.5" cy="8.5" r="7" fill="none" stroke="#444" stroke-width="1.6"/><path d="M8.5 4.5v4.5h3" fill="none" stroke="#444" stroke-width="1.6"/></svg></div>
  </div>
  <div class="row" style="top:583px"><label class="caption">Is the business registered as<br>a controlled waste carrier?</label>
    <div class="radios"><span class="radio"><span class="dot on"></span>Yes</span><span class="radio"><span class="dot"></span>No</span></div></div>
  <div class="row" style="top:656px"><label class="caption">Controlled waste carrier number</label><div class="field"></div></div>
  <div class="row" style="top:723px"><label class="caption">Is the business a registered<br>as a Dangerous goods carrier?</label>
    <div class="radios"><span class="radio"><span class="dot on"></span>Yes</span><span class="radio"><span class="dot"></span>No</span></div></div>
  <div class="row" style="top:800px"><label class="caption">Dangerous goods number</label><div class="field"></div></div>
  <div class="row" style="top:873px"><label class="caption">Wastes accepted (codes)</label><div class="field">Select Code<svg width="12" height="7" viewBox="0 0 12 7"><path d="M0 0h12L6 7z" fill="#333"/></svg></div></div>
  <div class="row" style="top:946px"><label class="caption">Wastes accepted (description)</label><div class="field hint">Bulk liquid/packaged/solid wastes</div></div>
  <div class="row" style="top:1022px"><label class="caption">Minimum volume of waste collected</label><div class="field hint">Number/L or Number/kg or Number/m</div></div>
  <div class="row" style="top:1094px"><label class="caption">Maximum volume of waste collected</label><div class="field hint">Number/L or Number/kg or Number/m</div></div>
  <div class="row" style="top:1167px"><label class="caption">Costs (for each type of waste collected<br>or all types of waste if the same cost for each)</label><div class="field hint">Dollars per kg, Litre, tonne, m3 per kilometre</div></div>
  <div class="row" style="top:1250px"><label class="caption">Would you like Tollin Waste to advertise<br>your carrier services on this website?</label>
    <div class="radios"><span class="radio"><span class="dot on"></span>Yes</span><span class="radio"><span class="dot"></span>No</span></div></div>
</form>
<div class="submit">Submit</div>

<footer class="site-footer">Copyright © 2018. All Rights Reserved</footer>
</body>
</html>
```